2 sided Handyman Postcard Design with coupon on the back

Company name is "Marlo QuickFix" Looking for a postcard that's also a business card. Showing Marlo QuickFix, 4817 Dunmore Hollow Rd NE, Brindle Falls, Ohio 43977, 740-318-6642, mtwelbeck@quillpost.example coupon- $25 off any job over $100, $50 off any job over $250, $75 off any job over $500, $100 off any job over $750, qualifications, experience 25 years. No job is to small. Handyman service. home repair. Free estimates. Examples, Flooring, Cabinets, Decks, Odd Jobs, Carpentry, Painting, Drywall repair, Ceramic tile, Screen repair, fence repair, Pressure wash, Hang a Picture, wood rot repair, Plumbing, Electrical, Small Jobs, Install ceiling fan, replace garbage disposal, toilet repair, install new lighting, Install safety grab bars, caulk tub or Kitchen, Hang Blinds/rods, Replace a switch/outlet, Replace/adjust doors and locksets, replace faucets/sinks/vanity tops, And much more. Have a signature look, I wear a aussie breezier hat on the job, full beard, and glasses. Am looking for a caricature of that with tools as main logo which should be shown on front and the back. One year warranty, Bonded, Insured. Cash or checks

```html
<!DOCTYPE html>
<html lang="en">
<head>
<meta charset="utf-8">
<title>Marlo QuickFix Handyman Postcard</title>
<link href="https://fonts.googleapis.com/css2?family=Arvo:wght@700&family=Lora:wght@400&family=Oswald:wght@600;700&family=Roboto:wght@400;700&family=Tinos:wght@400;700&family=Montserrat:wght@500&display=swap" rel="stylesheet">
<style>
  :root {
    --stage: #2b2b2b;
    --navy: #283f82;
    --navy-deep: #213671;
    --orange: #f07a2c;
    --orange-deep: #e2412a;
    --yellow: #f5e04a;
    --swoosh: #b3bedb;
    --white: #ffffff;
    --red: #e0202a;
    --coupon-bg: #f7f8fb;
    --bar-blue: #263d86;
    --phone-blue: #2b45a6;
  }
  * { margin: 0; padding: 0; box-sizing: border-box; }
  html, body { width: 1200px; height: 987px; overflow: hidden; background: var(--stage); }
  body { position: relative; font-family: 'Roboto', Arial, sans-serif; color: var(--white); }

  .card { position: absolute; left: 265px; width: 632px; overflow: hidden; background: var(--navy); }
  .card-front { top: 5px; height: 468px; }
  .card-back { top: 487px; height: 489px; }
  .card-bg { position: absolute; inset: 0; }

  .mascot {
    position: absolute; border-radius: 40px 40px 18px 18px;
    background: linear-gradient(180deg, #6b4a2a 0%, #7a5532 14%, #f0bf96 22%, #7a4a2c 32%, #2f60c2 42%, #2a55b0 85%, #5a3a22 100%);
  }
  .card-front .mascot { left: 22px; top: 22px; width: 142px; height: 340px; }
  .card-back .mascot { left: 22px; top: 28px; width: 142px; height: 378px; }

  .brand { position: absolute; font-family: 'Arvo', Georgia, serif; font-weight: 700; letter-spacing: 0.5px; white-space: nowrap; }
  .card-front .brand { left: 160px; top: 34px; font-size: 31px; }
  .card-back .brand { left: 166px; top: 22px; font-size: 26px; }

  .tagline { position: absolute; left: 164px; top: 70px; font-family: 'Lora', Georgia, serif; font-size: 20px; color: var(--yellow); }

  .badge { position: absolute; left: 462px; top: 8px; width: 134px; height: 134px; }

  .services-title { position: absolute; left: 198px; top: 127px; font-family: 'Roboto', Arial, sans-serif; font-weight: 700; font-size: 19px; color: var(--orange); }
  .services { position: absolute; top: 151px; list-style: none; font-weight: 700; font-size: 11px; line-height: 14.5px; white-space: nowrap; }
  .services li::before { content: "▪"; margin-right: 3px; font-size: 9px; }
  .col-1 { left: 198px; }
  .col-2 { left: 290px; }
  .col-3 { left: 413px; }

  .slogan { position: absolute; left: 284px; top: 296px; font-family: 'Arvo', Georgia, serif; font-size: 19px; }
  .call { position: absolute; left: 262px; top: 316px; display: flex; align-items: center; gap: 4px; font-family: 'Oswald', Impact, sans-serif; font-weight: 700; font-size: 33px; color: var(--orange); }
  .call svg { width: 22px; height: 28px; }

  .address { position: absolute; left: 42px; top: 393px; font-size: 15px; line-height: 17px; }
  .address strong { display: block; font-weight: 700; }
  .email { position: absolute; display: flex; align-items: center; gap: 8px; font-size: 17px; }
  .card-front .email { left: 360px; top: 426px; font-size: 16px; }
  .email svg { width: 26px; height: 18px; }

  .back-address { position: absolute; left: 168px; top: 56px; font-weight: 700; font-size: 13.5px; color: var(--yellow); }
  .experience { position: absolute; left: 190px; top: 116px; font-family: 'Montserrat', Arial, sans-serif; font-weight: 500; font-size: 17px; white-space: nowrap; }
  .experience b { font-family: 'Arvo', Georgia, serif; font-size: 27px; color: var(--yellow); vertical-align: -3px; }

  .coupons { position: absolute; left: 252px; top: 161px; width: 328px; height: 208px; background: var(--coupon-bg); border: 1.5px dashed #333; display: grid; grid-template-columns: 1fr 1fr; grid-template-rows: 1fr 1fr; }
  .coupon { display: flex; flex-direction: column; align-items: center; justify-content: center; }
  .coupon:nth-child(odd) { border-right: 1.5px dashed #333; }
  .coupon:nth-child(-n+2) { border-bottom: 1.5px dashed #333; }
  .amount { display: flex; align-items: flex-end; font-family: 'Tinos', 'Times New Roman', serif; color: #111; }
  .amount .value { font-size: 54px; line-height: 46px; color: var(--red); letter-spacing: -2px; }
  .amount .unit { display: flex; flex-direction: column; font-size: 22px; line-height: 20px; }
  .amount .unit span:first-child { font-size: 20px; }
  .condition { margin-top: 6px; padding: 1px 14px; background: var(--bar-blue); font-family: 'Tinos', 'Times New Roman', serif; font-size: 12px; white-space: nowrap; }
  .condition em { color: var(--yellow); font-weight: 700; }

  .call-today { position: absolute; left: 26px; top: 428px; font-family: 'Oswald', Impact, sans-serif; font-weight: 700; font-size: 24px; letter-spacing: -0.5px; }
  .call-today span { font-size: 31px; color: var(--phone-blue); }
  .card-back .email { left: 360px; top: 442px; font-size: 17px; }
</style>
</head>
<body>

<section class="card card-front">
  <svg class="card-bg" viewBox="0 0 632 468" preserveAspectRatio="none" aria-hidden="true">
    <defs>
      <linearGradient id="wave-front" x1="0" x2="1" y1="0" y2="0">
        <stop offset="0" stop-color="#e2412a"/>
        <stop offset="1" stop-color="#f27c2a"/>
      </linearGradient>
    </defs>
    <rect width="632" height="468" fill="#283f82"/>
    <path d="M162 172 C150 130 300 112 455 118 C320 124 178 138 175 172 Z" fill="#b3bedb"/>
    <path d="M560 308 C650 318 640 362 420 380 C600 360 625 322 560 308 Z" fill="#b3bedb"/>
    <path d="M0 284 C120 272 210 328 330 358 C450 384 560 384 632 372 L632 468 L0 468 Z" fill="#ffffff"/>
    <path d="M0 300 C120 290 210 344 330 372 C450 396 560 396 632 388 L632 468 L0 468 Z" fill="url(#wave-front)"/>
  </svg>

  <div class="mascot" role="img" aria-label="Caricature of a bearded handyman in a brimmed hat and glasses, wearing blue overalls, giving a thumbs up and holding a red toolbox"></div>

  <h1 class="brand">MARLO QUICKFIX</h1>
  <p class="tagline">Handyman Service</p>

  <svg class="badge" viewBox="0 0 134 134" aria-label="Free estimates">
    <polygon fill="#e0262a" points="67,4 78,26 100,12 100,37 126,36 111,57 131,72 107,82 118,106 92,103 86,128 67,111 48,128 42,103 16,106 27,82 3,72 23,57 8,36 34,37 34,12 56,26"/>
    <g transform="rotate(-12 67 67)" fill="#ffffff" text-anchor="middle" font-family="Arvo, Georgia, serif" font-weight="700">
      <text x="67" y="68" font-size="25">FREE</text>
      <text x="67" y="88" font-size="13">ESTIMATES</text>
    </g>
  </svg>

  <h2 class="services-title">SERVICES INCLUDES</h2>
  <ul class="services col-1">
    <li>Flooring,</li><li>Cabinets,</li><li>Decks,</li><li>Odd Jobs,</li><li>Carpentry,</li><li>Painting,</li><li>Drywall repair,</li><li>Ceramic tile,</li>
  </ul>
  <ul class="services col-2">
    <li>Screen repair,</li><li>Fence repair,</li><li>Pressure wash,</li><li>Hang a Picture,</li><li>Wood rot repair,</li><li>Plumbing, Electrical,</li><li>Small Jobs,</li><li>Install ceiling fan,</li><li>Toilet repair,</li>
  </ul>
  <ul class="services col-3">
    <li>Replace garbage disposal,</li><li>Install new lighting,</li><li>Install safety grab bars,</li><li>Caulk tub or Kitchen,</li><li>Hang Blinds/rods,</li><li>Replace a switch/outlet,</li><li>Replace/adjust doors and locksets,</li><li>Replace faucets/sinks/vanity tops,</li><li>And much more</li>
  </ul>

  <p class="slogan">NO JOB IS TOO SMALL</p>
  <p class="call">
    <svg viewBox="0 0 22 28" aria-hidden="true"><path d="M7 2 L11 2 L11 8 L8 9 C7 13 7 15 8 19 L11 20 L11 26 L7 26 C1 20 1 8 7 2 Z" fill="#ffffff"/></svg>
    CALL - 740-318-6642
  </p>

  <p class="address">Address<strong>4817 Dunmore Hollow Rd NE,</strong><strong>Brindle Falls, Ohio 43977</strong></p>
  <p class="email">
    <svg viewBox="0 0 26 18" aria-hidden="true"><rect x="1" y="1" width="24" height="16" fill="none" stroke="#1a1a1a" stroke-width="1.6"/><path d="M1 1 L13 10 L25 1 M1 17 L10 8 M25 17 L16 8" fill="none" stroke="#1a1a1a" stroke-width="1.6"/></svg>
    mtwelbeck@quillpost.example
  </p>
</section>

<section class="card card-back">
  <svg class="card-bg" viewBox="0 0 632 489" preserveAspectRatio="none" aria-hidden="true">
    <defs>
      <linearGradient id="wave-back" x1="0" x2="1" y1="0" y2="0">
        <stop offset="0" stop-color="#e2412a"/>
        <stop offset="1" stop-color="#f27c2a"/>
      </linearGradient>
    </defs>
    <rect width="632" height="489" fill="#283f82"/>
    <path d="M160 142 C150 100 300 82 440 88 C320 94 178 108 175 142 Z" fill="#b3bedb"/>
    <path d="M0 300 C120 290 210 350 330 380 C450 404 560 404 632 396 L632 489 L0 489 Z" fill="#ffffff"/>
    <path d="M0 316 C120 306 210 366 330 394 C450 416 560 414 632 408 L632 489 L0 489 Z" fill="url(#wave-back)"/>
  </svg>

  <div class="mascot" role="img" aria-label="Caricature of a bearded handyman in a brimmed hat and glasses, wearing blue overalls, giving a thumbs up and holding a red toolbox"></div>

  <h2 class="brand">MARLO QUICKFIX</h2>
  <p class="back-address">4817 Dunmore Hollow Rd NE, Brindle Falls, Ohio 43977</p>
  <p class="experience">QUALIFICATIONS, EXPERIENCE <b>25</b> YEARS</p>

  <div class="coupons">
    <div class="coupon">
      <div class="amount"><span class="value">25</span><span class="unit"><span>$</span><span>OFF</span></span></div>
      <p class="condition">Any Job Over <em>$100</em></p>
    </div>
    <div class="coupon">
      <div class="amount"><span class="value">50</span><span class="unit"><span>$</span><span>OFF</span></span></div>
      <p class="condition">Any Job Over <em>$250</em></p>
    </div>
    <div class="coupon">
      <div class="amount"><span class="value">75</span><span class="unit"><span>$</span><span>OFF</span></span></div>
      <p class="condition">Any Job Over <em>$500</em></p>
    </div>
    <div class="coupon">
      <div class="amount"><span class="value">100</span><span class="unit"><span>$</span><span>OFF</span></span></div>
      <p class="condition">Any Job Over <em>$750</em></p>
    </div>
  </div>

  <p class="call-today">CALL TODAY - <span>740-318-6642</span></p>
  <p class="email">Email - mtwelbeck@quillpost.example</p>
</section>

</body>
</html>
```